Veltrane Group Business Card Design

The CEO is looking for a new trendy look for his business card.
You can stay with current branding or come up with something new/creative. It can be 3D, including Medical Office buildings. You can use our logo in a variety of colors. Please include name, title, company name, company website, email address, cell number

Target Market(s)

Real Estate Development and Construction

Industry/Entity Type

Health care real estate

Contact Information for Business Card

Rohesh Kamdar, CEO M-604.781.2249 E-roheshkamdar@veltrane.com Address:4180 Lindqvist Ave, Tampa, FL 33482 www.veltrane.com

Font styles to use
Other font styles liked:
• Be creative

Requirements
Must have
• Creative, trendy look
Nice to have
• Please go to our website to get a feel- www. veltrane.com
Should not have
• small fonts

```html
<!DOCTYPE html>
<html lang="en">
<head>
<meta charset="utf-8">
<title>Veltrane Group Business Card</title>
<link rel="stylesheet" href="https://fonts.googleapis.com/css2?family=Montserrat:wght@400;700;800&display=swap">
<style>
  :root {
    --brand-red: #b01e2a;
    --ink: #2b2b2b;
    --card-white: #ffffff;
    --backdrop: #e6e6e6;
  }
  * { box-sizing: border-box; margin: 0; padding: 0; }
  html, body { width: 1200px; height: 900px; overflow: hidden; }
  body {
    background: var(--backdrop);
    font-family: "Montserrat", sans-serif;
    position: relative;
  }
  .card {
    position: absolute;
    width: 560px;
    height: 320px;
    border-radius: 18px;
    box-shadow: 0 10px 30px rgba(0,0,0,.18);
    overflow: hidden;
  }
  .card-front {
    left: 80px; top: 100px;
    background: var(--brand-red);
    display: flex; align-items: center; justify-content: center;
  }
  .front-wordmark {
    color: var(--card-white);
    font-weight: 800;
    font-size: 58px;
    letter-spacing: -1px;
  }
  .card-back {
    left: 560px; top: 480px;
    background: var(--card-white);
  }
  .back-wordmark {
    position: absolute; right: 34px; top: 30px;
    color: var(--brand-red);
    font-weight: 800;
    font-size: 40px;
    letter-spacing: -0.5px;
  }
  .address {
    position: absolute; right: 34px; top: 112px;
    text-align: right;
    color: var(--ink);
    font-size: 15px;
    line-height: 1.45;
  }
  .person {
    position: absolute; left: 34px; top: 140px;
  }
  .person-name {
    color: var(--brand-red);
    font-weight: 800;
    font-size: 24px;
    text-transform: uppercase;
    letter-spacing: .5px;
  }
  .person-title {
    color: var(--ink);
    font-size: 17px;
    margin-top: 2px;
  }
  .divider {
    position: absolute; left: 34px; right: 34px; top: 210px;
    height: 2px; background: var(--brand-red);
  }
  .contacts {
    position: absolute; left: 34px; top: 224px;
    list-style: none;
    color: var(--ink);
    font-size: 16px;
  }
  .contacts li { display: flex; align-items: center; gap: 10px; height: 26px; }
  .contacts svg { width: 14px; height: 14px; fill: var(--brand-red); flex: none; }
</style>
</head>
<body>
  <section class="card card-front" aria-label="Business card front">
    <span class="front-wordmark">Veltrane Group</span>
  </section>

  <section class="card card-back" aria-label="Business card back">
    <span class="back-wordmark">Veltrane Group</span>
    <p class="address">4180 Lindqvist Ave,<br>Tampa, FL 33482</p>
    <div class="person">
      <p class="person-name">Rohesh Kamdar</p>
      <p class="person-title">CEO</p>
    </div>
    <div class="divider"></div>
    <ul class="contacts">
      <li>
        <svg viewBox="0 0 14 14" aria-hidden="true"><path d="M3 0h8a1 1 0 0 1 1 1v12a1 1 0 0 1-1 1H3a1 1 0 0 1-1-1V1a1 1 0 0 1 1-1zm1 2v9h6V2z"/></svg>
        604.781.2249
      </li>
      <li>
        <svg viewBox="0 0 14 14" aria-hidden="true"><path d="M0 2h14v10H0zm1.5 1.2L7 7.5l5.5-4.3z"/></svg>
        roheshkamdar@veltrane.com
      </li>
      <li>
        <svg viewBox="0 0 14 14" aria-hidden="true"><circle cx="7" cy="7" r="7"/><path d="M1 7h12M7 1c-2.5 3-2.5 9 0 12M7 1c2.5 3 2.5 9 0 12" stroke="#fff" stroke-width="1" fill="none"/></svg>
        www.veltrane.com
      </li>
    </ul>
  </section>
</body>
</html>
```